Website for International Non-Profit for Birth Parent Searching

LumaKin is a 501(c)(3) non-profit organization that helps Chinese adoptees search and reunite with birth families who were separated due the One Child Policy in China. We want to create a website that can link to an information database that allows website users to easily access information around search ads in an organized way; help connect families to professional searchers; provide resources for community support for adoptees and their families as they embark on a personal and emotional journey of finding birth family through support groups on social media and consultation/education on the searching process; and provide the opportunity for the adoptive community to give back through donations and volunteer opportunities. The final design should foster a sense of community and be easy navigable to access the multiple resources we provide to help families search for each other. We would like to see designs with red/black/white color schemes that are gentle, inviting, and family friendly to viewers. We would like to see some design layouts with Chinese themes, if possible.

```html
<!DOCTYPE html>
<html lang="en">
<head>
<meta charset="utf-8">
<title>LumaKin — Birth Parent Searching</title>
<link rel="stylesheet" href="https://fonts.googleapis.com/css2?family=Rubik:wght@500;600;700&family=Roboto:wght@400;500;700&display=swap">
<style>
:root{
  --red:#e0101f;
  --red-deep:#c50d1a;
  --ink:#111111;
  --text:#666666;
  --soft:#f2f2f2;
  --footer:#555555;
  --white:#ffffff;
}
*{box-sizing:border-box;margin:0;padding:0}
html,body{width:1200px;height:3889px;overflow:hidden}
body{position:relative;font-family:"Roboto",Arial,sans-serif;color:var(--text);background:var(--white)}
h1,h2,h3{font-family:"Rubik","Roboto",sans-serif;color:var(--ink)}
.btn{position:absolute;background:var(--red);color:var(--white);font:500 14px "Roboto",sans-serif;text-transform:uppercase;display:flex;align-items:center;justify-content:center;border-radius:2px}

/* header */
.site-header{position:absolute;left:0;top:0;width:1200px;height:74px;background:var(--white);box-shadow:0 1px 4px rgba(0,0,0,.08);z-index:2}
.brand{position:absolute;left:110px;top:20px;display:flex;align-items:center;gap:12px;font:700 25px "Rubik",sans-serif;color:var(--red)}
.brand-dot{width:36px;height:36px;border-radius:50%;background:var(--red)}
.main-nav{position:absolute;left:404px;top:29px;display:flex;gap:26px;font:500 13.5px "Roboto",sans-serif;color:var(--ink);text-transform:uppercase}
.main-nav .active{color:var(--red)}

/* hero */
.hero{position:absolute;left:0;top:74px;width:1200px;height:557px;background:linear-gradient(100deg,#c6cfc0 0%,#d6dbd2 35%,#c3cabf 60%,#8fa57b 100%)}
.hero-photo{position:absolute;inset:0;background:linear-gradient(180deg,rgba(255,255,255,0) 60%,rgba(110,150,70,.55) 100%)}
.hero h1{position:absolute;left:110px;top:136px;width:560px;font:700 38px/47px "Rubik",sans-serif;color:var(--white);text-transform:uppercase;text-shadow:0 2px 6px rgba(0,0,0,.35)}
.hero p{position:absolute;left:110px;top:292px;width:520px;font:500 15px/26px "Roboto",sans-serif;color:var(--white);text-shadow:0 1px 4px rgba(0,0,0,.55)}
.hero .btn{left:110px;top:363px;width:146px;height:48px}
.slide-arrow{position:absolute;top:260px;width:38px;height:38px;border-radius:50%;background:var(--white);display:flex;align-items:center;justify-content:center}

/* who we are */
.who-photo-main{position:absolute;left:94px;top:759px;width:372px;height:372px;border-radius:50%;border:4px solid var(--white);box-shadow:0 2px 8px rgba(0,0,0,.15);background:linear-gradient(160deg,#f3ece4,#d9c2ab 60%,#b59c88)}
.who-photo-small{position:absolute;left:342px;top:947px;width:198px;height:198px;border-radius:50%;border:4px solid var(--white);box-shadow:0 2px 8px rgba(0,0,0,.18);background:linear-gradient(160deg,#dfe6ee,#c7cdd6 55%,#a8aab8)}
.who h2{position:absolute;left:605px;top:748px;font:700 38px "Rubik",sans-serif}
.who p{position:absolute;left:605px;top:812px;width:495px;font:400 15px/30px "Roboto",sans-serif}
.who .btn{left:605px;top:1102px;width:146px;height:48px}

/* organized way */
.organized{position:absolute;left:0;top:1260px;width:1200px;height:634px;background:linear-gradient(180deg,#f1f1f1,#ececec 60%,#f4f4f4)}
.organized h2{position:absolute;left:0;width:1200px;top:78px;text-align:center;font:700 34px "Rubik",sans-serif}
.organized-photo{position:absolute;left:104px;top:185px;width:444px;height:354px;border:4px solid var(--white);box-shadow:0 2px 8px rgba(0,0,0,.12);background:linear-gradient(135deg,#eaeaea,#cdb6c4 45%,#5f8ea4 80%,#3d5d78)}
.aim{position:absolute;left:605px;display:flex;gap:30px}
.aim svg{flex:none}
.aim p{width:420px;font:500 13.5px/25px "Roboto",sans-serif;color:#555;text-transform:uppercase}

/* work for children */
.work h2{position:absolute;left:0;width:1200px;top:1983px;text-align:center;font:700 34px "Rubik",sans-serif}
.work-card{position:absolute;top:2078px;width:238px;height:272px;display:flex;align-items:flex-end;justify-content:center;padding-bottom:36px;color:var(--white);font:500 13.5px "Roboto",sans-serif;text-transform:uppercase}

/* finding ads */
.finding{position:absolute;left:0;top:2466px;width:1200px;height:255px;background:linear-gradient(90deg,var(--red) 0%,var(--red) 38%,#ee6f7a 58%,#f3c5c8 80%,#f0d2cf 100%)}
.finding h2{position:absolute;left:108px;top:62px;font:700 30px "Rubik",sans-serif;color:var(--white)}
.finding p{position:absolute;left:108px;top:114px;width:500px;font:400 14px/25px "Roboto",sans-serif;color:var(--white)}

/* help */
.help h2{position:absolute;left:0;width:1200px;top:2806px;text-align:center;font:700 34px "Rubik",sans-serif}
.help-card{position:absolute;top:2898px;width:305px}
.help-frame{position:absolute;left:0;top:0;width:305px;height:60px;border:10px solid var(--red);border-bottom:none}
.help-photo{position:absolute;left:10px;top:10px;width:285px;height:202px}
.help-card h3{position:absolute;left:24px;top:234px;font:600 17px "Rubik",sans-serif;text-transform:uppercase}
.help-rule{position:absolute;left:24px;top:263px;width:30px;height:2px;background:var(--red)}
.help-card p{position:absolute;left:24px;top:280px;width:265px;font:400 14px/23px "Roboto",sans-serif}

/* stats */
.stats{position:absolute;left:0;top:3335px;width:1200px;height:265px;background:linear-gradient(90deg,var(--red-deep),var(--red) 50%,var(--red-deep))}
.stat{position:absolute;top:50px;width:250px;text-align:center;color:var(--white)}
.stat h4{font:500 15px "Roboto",sans-serif;text-transform:uppercase}
.stat svg{display:block;margin:14px auto 0}
.stat strong{display:block;margin-top:8px;font:600 33px "Rubik",sans-serif}

/* footer */
.site-footer{position:absolute;left:0;top:3600px;width:1200px;height:289px;background:var(--footer);color:#eee}
.footer-brand{position:absolute;left:118px;top:74px;display:flex;align-items:center;gap:14px;font:600 24px "Rubik",sans-serif;color:var(--white)}
.footer-brand span.dot{width:36px;height:36px;border-radius:50%;background:var(--white)}
.social{position:absolute;left:118px;top:133px;display:flex;gap:8px}
.social span{width:34px;height:34px}
.copy{position:absolute;left:118px;top:195px;font:400 13.5px "Roboto",sans-serif}
.f-col{position:absolute;top:75px;font:400 13.5px/30px "Roboto",sans-serif}
.f-col h5{font:500 13.5px "Roboto",sans-serif;color:var(--white);text-transform:uppercase;margin-bottom:12px}
.f-col li{list-style:none}
.f-col.links li::before{content:"»";margin-right:12px}
</style>
</head>
<body>

<header class="site-header">
  <div class="brand"><span class="brand-dot"></span>LUMAKIN</div>
  <nav class="main-nav">
    <span class="active">Home</span><span>Who We Are</span><span>What We Are</span><span>Ways To Help</span><span>Contact Us</span>
  </nav>
  <div class="btn" style="left:984px;top:14px;width:103px;height:46px">Donate</div>
</header>

<section class="hero" role="img" aria-label="Family sitting together on a picnic blanket in a park, parent reading a red book to a child">
  <div class="hero-photo"></div>
  <h1>We are an international non-profit for birth parent searching</h1>
  <p>Lorem ipsum dolor sit amet, consectetur adipiscing elit, sed do eiusmod tempor incididunt ut labore et dolore magna aliqua.</p>
  <div class="btn">Serach Ads</div>
  <div class="slide-arrow" style="left:33px"><svg width="14" height="14" viewBox="0 0 14 14"><path d="M9 1 3 7l6 6" fill="none" stroke="#111" stroke-width="2"/></svg></div>
  <div class="slide-arrow" style="left:1129px"><svg width="14" height="14" viewBox="0 0 14 14"><path d="m5 1 6 6-6 6" fill="none" stroke="#111" stroke-width="2"/></svg></div>
</section>

<section class="who">
  <div class="who-photo-main" role="img" aria-label="Laughing family on a beach with a child riding on a parent's shoulders"></div>
  <div class="who-photo-small" role="img" aria-label="Smiling schoolgirl with arms spread wide"></div>
  <h2>WHO WE ARE</h2>
  <p>Lorem ipsum dolor sit amet, consectetur adipiscing elit, sed do eiusmod tempor incididunt ut labore et dolore magna aliqua. Ut enim ad minim veniam, quis nostrud exercitation ullamco laboris nisi ut aliquip ex ea commodo consequat. Lorem ipsum dolor sit amet, consectetur adipiscing elit, sed do eiusmod tempor incididunt ut labore et dolore magna aliqua. Ut enim ad minim veniam, quis nostrud exercitation ullamco laboris nisi ut aliquip ex ea commodo consequat. Lorem ipsum dolor sit amet, consectetur adipiscing elit, sed do eiusmod tempor incididunt ut labore et dolore magna aliqua.</p>
  <div class="btn">Learn More</div>
</section>

<section class="organized">
  <h2>OUR ORGANIZED WAY</h2>
  <div class="organized-photo" role="img" aria-label="Parents sitting on the floor playing with their baby"></div>
  <div class="aim" style="top:212px">
    <svg width="40" height="38" viewBox="0 0 40 38" fill="none" stroke="#e0101f" stroke-width="2"><circle cx="13" cy="10" r="6"/><circle cx="27" cy="10" r="6"/><path d="M2 36v-8a8 8 0 0 1 8-8h6a8 8 0 0 1 8 8v8M18 36v-8a8 8 0 0 1 8-8h4a8 8 0 0 1 8 8v8"/></svg>
    <p>Help connect families to professional searchers</p>
  </div>
  <div class="aim" style="top:287px">
    <svg width="40" height="38" viewBox="0 0 40 38" fill="none" stroke="#e0101f" stroke-width="2"><circle cx="13" cy="10" r="6"/><circle cx="27" cy="10" r="6"/><path d="M2 36v-8a8 8 0 0 1 8-8h6a8 8 0 0 1 8 8v8M18 36v-8a8 8 0 0 1 8-8h4a8 8 0 0 1 8 8v8"/></svg>
    <p>Provide resources for community support for adoptees &amp; their families as they embark on a personal and emotional journey of finding birth family through support groups on social media &amp; consultation/education on the searching process</p>
  </div>
  <div class="aim" style="top:443px">
    <svg width="40" height="38" viewBox="0 0 40 38" fill="none" stroke="#e0101f" stroke-width="2"><circle cx="13" cy="10" r="6"/><circle cx="27" cy="10" r="6"/><path d="M2 36v-8a8 8 0 0 1 8-8h6a8 8 0 0 1 8 8v8M18 36v-8a8 8 0 0 1 8-8h4a8 8 0 0 1 8 8v8"/></svg>
    <p>Provide the opportunity for the adoptive community to give back through donations and volunteer opportunities</p>
  </div>
</section>

<section class="work">
  <h2>OUR WORK FOR CHILDREN</h2>
  <div class="work-card" style="left:110px;background:linear-gradient(180deg,#f1e4dc 0%,#e8b9bd 60%,#e58891 100%)" role="img" aria-label="Young girl writing at a desk">The opportunity to learn</div>
  <div class="work-card" style="left:357px;background:linear-gradient(180deg,#e9e6e3 0%,#c79ea2 60%,#b8737b 100%)" role="img" aria-label="Parent talking with a small child on a sofa">Protection from harm</div>
  <div class="work-card" style="left:604px;background:linear-gradient(180deg,#f3f0ee 0%,#eec5c8 60%,#e98c95 100%)" role="img" aria-label="Girl sitting cross-legged meditating">A healthy start in life</div>
  <div class="work-card" style="left:851px;background:linear-gradient(180deg,#ede7e0 0%,#d7a9a6 60%,#c77a7f 100%)" role="img" aria-label="Patient resting in a hospital room">Emergency response</div>
</section>

<section class="finding" role="img" aria-label="Smiling family hugging, parents with a young daughter">
  <h2>FINDING ADS</h2>
  <p>Sed ut perspiciatis unde omnis iste natus error sit voluptatem accusantium doloremque laudantium, totam rem aperiam, eaque ipsa quae ab illo inventore veritatis et quasi architecto beatae vitae</p>
</section>

<section class="help">
  <h2>HOW CAN WE HELP</h2>
  <div class="help-card" style="left:110px">
    <div class="help-frame"></div>
    <div class="help-photo" role="img" aria-label="Smiling baby crawling on the floor" style="background:linear-gradient(160deg,#f2efec,#e2d6cf 60%,#cdbdb4)"></div>
    <h3>Donate</h3><div class="help-rule"></div>
    <p>Sed ut perspiciatis unde omnis iste natus error sit voluptatem accusantium doloremque laudantium</p>
  </div>
  <div class="help-card" style="left:447px">
    <div class="help-frame"></div>
    <div class="help-photo" role="img" aria-label="Child in a red traditional dress in front of a wooden window" style="background:linear-gradient(180deg,#4a2a26,#6e3b33 55%,#c0262c 100%)"></div>
    <h3>Sponsor a child</h3><div class="help-rule"></div>
    <p>Sed ut perspiciatis unde omnis iste natus error sit voluptatem accusantium doloremque laudantium</p>
  </div>
  <div class="help-card" style="left:784px">
    <div class="help-frame"></div>
    <div class="help-photo" role="img" aria-label="Excited child in a yellow sweater outdoors" style="background:linear-gradient(160deg,#d9dfe4,#e9d9b8 55%,#e5b92a 100%)"></div>
    <h3>Shop gift catalog</h3><div class="help-rule"></div>
    <p>Sed ut perspiciatis unde omnis iste natus error sit voluptatem accusantium doloremque laudantium</p>
  </div>
</section>

<section class="stats">
  <div class="stat" style="left:105px"><h4>Healthy Children</h4>
    <svg width="84" height="84" viewBox="0 0 84 84"><circle cx="42" cy="42" r="40" fill="#fff"/><circle cx="42" cy="42" r="32" fill="#e0101f"/><circle cx="42" cy="34" r="8" fill="none" stroke="#fff" stroke-width="2.5"/><path d="M30 58v-6a8 8 0 0 1 8-8h8a8 8 0 0 1 8 8v6z" fill="none" stroke="#fff" stroke-width="2.5"/></svg>
    <strong>13,789</strong></div>
  <div class="stat" style="left:352px"><h4>Children Educated</h4>
    <svg width="84" height="84" viewBox="0 0 84 84"><circle cx="42" cy="42" r="40" fill="#fff"/><circle cx="42" cy="42" r="32" fill="#111"/><rect x="27" y="30" width="30" height="20" fill="none" stroke="#fff" stroke-width="2.5"/><path d="M36 56h12M42 50v6" stroke="#fff" stroke-width="2.5"/></svg>
    <strong>100+</strong></div>
  <div class="stat" style="left:599px"><h4>Protected From Harm</h4>
    <svg width="84" height="84" viewBox="0 0 84 84"><circle cx="42" cy="42" r="40" fill="#fff"/><circle cx="42" cy="42" r="32" fill="#e0101f"/><path d="M42 24l14 5v10c0 10-6 17-14 20-8-3-14-10-14-20V29z" fill="none" stroke="#fff" stroke-width="2.5"/><rect x="37" y="40" width="10" height="8" fill="#fff"/></svg>
    <strong>50</strong></div>
  <div class="stat" style="left:846px"><h4>Lifted From Poverty</h4>
    <svg width="84" height="84" viewBox="0 0 84 84" fill="none" stroke="#fff" stroke-width="2.2"><circle cx="42" cy="42" r="40" fill="#fff" stroke="none"/><circle cx="42" cy="42" r="32" fill="#111" stroke="none"/><circle cx="31" cy="29" r="4"/><circle cx="42" cy="26" r="4.5"/><circle cx="53" cy="29" r="4"/><path d="M24 44v-4a5 5 0 0 1 5-5h4M60 44v-4a5 5 0 0 0-5-5h-4M34 44v-5a5 5 0 0 1 5-5h6a5 5 0 0 1 5 5v5"/><path d="M22 49h30l6 4h6M22 49v10h26l14-6"/></svg>
    <strong>3000</strong></div>
</section>

<footer class="site-footer">
  <div class="footer-brand"><span class="dot"></span>LUMAKIN</div>
  <div class="social" aria-label="Social media links">
    <span style="background:#3b5998"></span><span style="background:#1da1f2"></span><span style="background:#d42428"></span>
  </div>
  <div class="copy">© 2021 LumaKin. All Rights Reserved.</div>
  <div class="f-col" style="left:446px"><h5>Contact Us</h5>
    <ul><li>218 Maple Harbor Lane</li><li>United States</li><li>Mail&nbsp; : &nbsp;info@lumakin.org</li><li>Tel&nbsp;&nbsp;&nbsp;&nbsp; : &nbsp;1 800 555 0142</li></ul></div>
  <div class="f-col links" style="left:737px"><h5>Menu</h5>
    <ul><li>Home</li><li>About</li><li>What We Do</li><li>Contact Us</li></ul></div>
  <div class="f-col links" style="left:934px"><h5>Useful Links</h5>
    <ul><li>FAQ</li><li>Terms &amp; Conditions</li><li>Privacy policy</li><li>Donate</li></ul></div>
</footer>

</body>
</html>
```